Wordpress Design Project (Nerith)

We need a wordpress design for an established auction and real estate company based in Pennsylvania. The winning design will incorporate a professional layout with and company logo in a very simple and clean layout.

Industry/Entity Type

Real Estate

Requirements
Must have
• Navigation:
1) Home; 2) Auctions; 3) Appraisals; 4) Real Estate; 5) FAQ; 6) About Us; 7) Contact Us.

Site will have overall layout of https://www.plumvarro.com/featured/regions/the-northeast. Home page will have logo and navigation at top. The navigation bar will also have social media icons (facebook, Google+, RSS, twitter) inside it. There will be text in the content area - use lorem ipsum. The image attached will be used below text (auctions.jpg) . Footer will have smaller company loogo, the attached affiliation logos and social media icons.

Logo attached. Color scheme will be black, gray, and red as accent color.
Nice to have
• navigation will have dropdowns, nice to have one represented - under auctions 'All Auctions' will be dropdown.

```html
<!DOCTYPE html>
<html lang="en">
<head>
<meta charset="utf-8">
<title>Nerith — Auctions, Appraisals & Real Estate</title>
<link href="https://fonts.googleapis.com/css2?family=Source+Sans+3:wght@400;600;700&display=swap" rel="stylesheet">
<style>
:root{
  --red:#c0272d;
  --red-dark:#a11f24;
  --ink:#333333;
  --muted:#666666;
  --line:#dcdcdc;
  --panel:#f4f4f4;
  --topbar:#efefef;
  --footer:#2b2b2b;
  --footer-text:#dddddd;
  --chip:#d6d6d6;
}
*{box-sizing:border-box;margin:0;padding:0}
html,body{width:1200px;height:2353px;overflow:hidden}
body{position:relative;background:#fff;font-family:"Source Sans 3",Arial,sans-serif;color:var(--ink)}
a{color:inherit;text-decoration:none}
.abs{position:absolute}

/* top utility bar */
.utility-bar{left:0;top:0;width:1200px;height:50px;background:var(--topbar);border-bottom:1px solid #e2e2e2}
.utility-links{right:89px;top:15px;display:flex;gap:14px;font-size:13px;font-weight:600;text-transform:uppercase;letter-spacing:.2px}
.utility-links .accent{color:var(--red)}
.utility-links .sep{color:#999}
.utility-links .cart{display:flex;align-items:center;gap:6px}

/* header */
.site-header{left:0;top:50px;width:1200px;height:118px;background:linear-gradient(#fff,#f7f7f7);border-bottom:1px solid var(--line)}
.brand{left:89px;top:76px;display:flex;align-items:center;gap:12px}
.brand-mark{width:62px;height:62px;background:var(--red)}
.brand-name{font-size:46px;font-weight:700;color:#222;letter-spacing:1px}
.search{left:662px;top:62px;width:271px;height:28px;border:1px solid #cfcfcf;background:#fff;display:flex;align-items:center;justify-content:space-between;padding-left:10px;font-size:13px;color:#999}
.search-btn{width:26px;height:26px;background:#8a8a8a;display:flex;align-items:center;justify-content:center}
.social{display:flex;gap:14px}
.social span{display:block;width:30px;height:30px;border:1px solid #cfcfcf;background:#f2f2f2;border-radius:3px}
.header-social{left:955px;top:62px}
.main-nav{right:89px;top:128px;display:flex;gap:32px;font-size:16px;color:#444}
.main-nav a{position:relative;padding-bottom:14px}
.main-nav a.current{color:var(--red)}
.main-nav a.current::after{content:"";position:absolute;left:-4px;right:-4px;bottom:0;height:3px;background:var(--red)}

/* slider */
.hero{left:89px;top:185px;width:1022px;height:339px;background:var(--panel);border:1px solid var(--line);padding:10px}
.hero-media{width:1000px;height:318px;background:linear-gradient(90deg,#dadde0 0%,#f4f4f4 40%,#fafafa 70%,#e6d4c6 100%)}
.hero-copy{left:566px;top:218px;width:478px}
.hero-copy h1{font-size:27px;font-weight:700;color:var(--red);line-height:1.2;white-space:nowrap;letter-spacing:-.2px}
.hero-copy p{margin-top:7px;font-size:14px;line-height:25px;color:#444}
.btn-start{left:566px;top:350px;width:204px;height:47px;background:linear-gradient(#4a4a4a,#2a2a2a);color:#fff;font-size:17px;font-weight:600;display:flex;align-items:center;justify-content:center;gap:8px;border-radius:3px}
.hero-arrow{top:334px;width:40px;height:40px;border-radius:50%;background:#fff;border:1px solid #d0d0d0;display:flex;align-items:center;justify-content:center}

/* listing cards */
.card{width:502px;height:305px;border:1px solid var(--line);background:linear-gradient(#fff 70%,#f3f3f3);padding:11px}
.card-photo{width:478px;height:220px;border:1px solid #999}
.card-title{position:absolute;left:23px;top:248px;font-size:14.5px;font-weight:700;color:var(--red)}
.card-text{position:absolute;left:23px;top:271px;font-size:14px;color:#444}
.card-place{position:absolute;right:10px;top:250px;display:flex;gap:8px;font-size:13.5px;line-height:1.2;color:#555}

/* pagination */
.pagination{left:0;width:1200px;top:1905px;display:flex;justify-content:center;gap:4px}
.pagination span{width:23px;height:23px;background:var(--chip);border-radius:3px;font-size:11px;color:#fff;display:flex;align-items:center;justify-content:center}
.pagination span.active{background:#8e8e8e}
.pagination span.gap{background:none;color:#999}

/* affiliations & mailing list */
.rule{left:89px;width:1022px;height:1px;background:var(--line)}
.section-title{font-size:21px;font-weight:600;color:var(--red)}
.affiliations{left:130px;top:2008px}
.badges{left:264px;top:2008px;display:grid;grid-template-columns:repeat(3,62px);column-gap:46px;row-gap:18px}
.badges span{width:56px;height:52px;background:#cfcfcf}
.badges span.round{border-radius:50%}
.vrule{left:601px;top:1995px;width:1px;height:146px;background:var(--line)}
.mailing{left:642px;top:2008px}
.mailing p{margin-top:10px;width:160px;font-size:14px;line-height:1.6;color:#555}
.mail-field{left:813px;top:2053px;width:263px;height:39px;border:1px solid #d0d0d0;display:flex;align-items:center;justify-content:space-between;padding:0 8px 0 12px;font-size:13.5px;color:#999}
.mail-go{width:26px;height:26px;border:1px solid #d0d0d0;display:flex;align-items:center;justify-content:center}

/* footer */
.site-footer{left:0;top:2179px;width:1200px;height:174px;background:var(--footer);color:var(--footer-text)}
.footer-nav{left:89px;top:30px;display:flex;gap:12px;font-size:14px}
.footer-nav .sep{color:#888}
.copyright{left:89px;top:66px;font-size:14px}
.footer-social{left:89px;top:108px;gap:14px}
.footer-social span{width:28px;height:28px;background:#cfcfcf;border:none}
.footer-brand{left:860px;top:33px;width:251px;height:72px;background:#e9e9e9;border:1px solid #bbb;display:flex;align-items:center;justify-content:center;gap:10px}
.footer-brand .brand-mark{width:40px;height:40px}
.footer-brand .brand-name{font-size:32px}
.footer-legal{right:89px;top:124px;display:flex;gap:10px;font-size:14px}
.to-top{left:586px;top:126px;width:30px;text-align:center;font-size:10px;color:#aaa}
.to-top span{display:block;margin:4px auto 0;width:28px;height:28px;border-radius:50%;border:2px solid #aaa;display:flex;align-items:center;justify-content:center}
</style>
</head>
<body>

<div class="utility-bar abs"></div>
<nav class="utility-links abs">
  <a class="accent" href="#">Register</a><span class="sep">::</span>
  <a class="accent" href="#">Login</a><span class="sep">::</span>
  <a href="#">My Account</a><span class="sep">::</span>
  <a class="cart" href="#"><svg width="16" height="14" viewBox="0 0 16 14"><path d="M1 1h3l2 8h8l2-6H5" fill="none" stroke="#333" stroke-width="1.6"/><circle cx="7" cy="12" r="1.3" fill="#333"/><circle cx="13" cy="12" r="1.3" fill="#333"/></svg>My Cart - <span style="text-transform:none">(cart empty)</span></a>
</nav>

<header class="site-header abs"></header>
<a class="brand abs" href="#"><span class="brand-mark"></span><span class="brand-name">Nerith</span></a>
<div class="search abs">Search<span class="search-btn"><svg width="14" height="14" viewBox="0 0 14 14"><circle cx="6" cy="6" r="4" fill="none" stroke="#fff" stroke-width="1.8"/><path d="M9 9l4 4" stroke="#fff" stroke-width="1.8"/></svg></span></div>
<div class="social header-social abs" aria-label="Social links"><span></span><span></span><span></span><span></span></div>
<nav class="main-nav abs">
  <a class="current" href="#">Home</a><a href="#">Auctions</a><a href="#">Appraisals</a><a href="#">Real Estate</a><a href="#">FAQ</a><a href="#">About Us</a><a href="#">Contact Us</a>
</nav>

<section class="hero abs">
  <div class="hero-media" role="img" aria-label="Smiling woman using a laptop beside an auction gavel"></div>
</section>
<div class="hero-copy abs">
  <h1>Mauris suscipit fermentum leo et tempus</h1>
  <p>Suspendisse sit amet dolor eu ligula dapibus facilisis sit amet cursus mi. Cum sociis natoque penatibus et magnis dis parturient montes, nascetur ridiculus mus elit elit, aliquam vel faucibus nec.</p>
</div>
<a class="btn-start abs" href="#">GET STARTED NOW <span>»</span></a>
<span class="hero-arrow abs" style="left:120px"><svg width="10" height="14" viewBox="0 0 10 14"><path d="M7 2L2 7l5 5" fill="none" stroke="#888" stroke-width="1.6"/></svg></span>
<span class="hero-arrow abs" style="left:1039px"><svg width="10" height="14" viewBox="0 0 10 14"><path d="M3 2l5 5-5 5" fill="none" stroke="#888" stroke-width="1.6"/></svg></span>

<!-- listings -->
<article class="card abs" style="left:89px;top:558px">
  <div class="card-photo" role="img" aria-label="Rows of wooden cabinets in a warehouse" style="background:linear-gradient(90deg,#c9a07a,#6e2a22 45%,#8a4a3a)"></div>
  <h3 class="card-title">Curabitur luctus dignissim</h3><p class="card-text">Aenean lectus ligula, viverra vitae dui id</p>
  <div class="card-place"><svg width="14" height="20" viewBox="0 0 14 20"><path d="M7 1a6 6 0 0 1 6 6c0 4-6 12-6 12S1 11 1 7a6 6 0 0 1 6-6z" fill="#d8623a"/><circle cx="7" cy="7" r="2.2" fill="#fff"/></svg><span>Carrowfield,<br>MD</span></div>
</article>
<article class="card abs" style="left:609px;top:558px">
  <div class="card-photo" role="img" aria-label="Bathroom vanities with granite tops" style="background:linear-gradient(160deg,#8d6a4e,#b27a45 50%,#3a2f2a)"></div>
  <h3 class="card-title">Curabitur luctus dignissim</h3><p class="card-text">Aenean lectus ligula, viverra vitae dui id</p>
  <div class="card-place"><svg width="14" height="20" viewBox="0 0 14 20"><path d="M7 1a6 6 0 0 1 6 6c0 4-6 12-6 12S1 11 1 7a6 6 0 0 1 6-6z" fill="#d8623a"/><circle cx="7" cy="7" r="2.2" fill="#fff"/></svg><span>Carrowfield,<br>MD</span></div>
</article>
<article class="card abs" style="left:89px;top:893px">
  <div class="card-photo" role="img" aria-label="Rolled carpets with yellow tags" style="background:linear-gradient(135deg,#b9c4c7,#7d7a6d 50%,#5e6062)"></div>
  <h3 class="card-title">Curabitur luctus dignissim</h3><p class="card-text">Aenean lectus ligula, viverra vitae dui id</p>
  <div class="card-place"><svg width="14" height="20" viewBox="0 0 14 20"><path d="M7 1a6 6 0 0 1 6 6c0 4-6 12-6 12S1 11 1 7a6 6 0 0 1 6-6z" fill="#d8623a"/><circle cx="7" cy="7" r="2.2" fill="#fff"/></svg><span>Carrowfield,<br>MD</span></div>
</article>
<article class="card abs" style="left:609px;top:893px">
  <div class="card-photo" role="img" aria-label="Row of white paneled doors" style="background:linear-gradient(90deg,#9fb0c0,#e8e8e6 40%,#d7d3cc 80%,#b59063)"></div>
  <h3 class="card-title">Curabitur luctus dignissim</h3><p class="card-text">Aenean lectus ligula, viverra vitae dui id</p>
  <div class="card-place"><svg width="14" height="20" viewBox="0 0 14 20"><path d="M7 1a6 6 0 0 1 6 6c0 4-6 12-6 12S1 11 1 7a6 6 0 0 1 6-6z" fill="#d8623a"/><circle cx="7" cy="7" r="2.2" fill="#fff"/></svg><span>Carrowfield,<br>MD</span></div>
</article>
<article class="card abs" style="left:89px;top:1227px">
  <div class="card-photo" role="img" aria-label="Wooden double doors and folding partition" style="background:linear-gradient(90deg,#d8c9b2,#b8652c 40%,#8c5a33 60%,#d9c8a8)"></div>
  <h3 class="card-title">Curabitur luctus dignissim</h3><p class="card-text">Aenean lectus ligula, viverra vitae dui id</p>
  <div class="card-place"><svg width="14" height="20" viewBox="0 0 14 20"><path d="M7 1a6 6 0 0 1 6 6c0 4-6 12-6 12S1 11 1 7a6 6 0 0 1 6-6z" fill="#d8623a"/><circle cx="7" cy="7" r="2.2" fill="#fff"/></svg><span>Carrowfield,<br>MD</span></div>
</article>
<article class="card abs" style="left:609px;top:1227px">
  <div class="card-photo" role="img" aria-label="Conference hall with folding wall panels" style="background:linear-gradient(160deg,#6b5448,#c46a2a 35%,#d8cbbd 70%,#b39a86)"></div>
  <h3 class="card-title">Curabitur luctus dignissim</h3><p class="card-text">Aenean lectus ligula, viverra vitae dui id</p>
  <div class="card-place"><svg width="14" height="20" viewBox="0 0 14 20"><path d="M7 1a6 6 0 0 1 6 6c0 4-6 12-6 12S1 11 1 7a6 6 0 0 1 6-6z" fill="#d8623a"/><circle cx="7" cy="7" r="2.2" fill="#fff"/></svg><span>Carrowfield,<br>MD</span></div>
</article>
<article class="card abs" style="left:89px;top:1561px">
  <div class="card-photo" role="img" aria-label="Brown leather sofas in a lounge" style="background:linear-gradient(160deg,#c9d3c8,#9a6a4e 45%,#5d3526)"></div>
  <h3 class="card-title">Curabitur luctus dignissim</h3><p class="card-text">Aenean lectus ligula, viverra vitae dui id</p>
  <div class="card-place"><svg width="14" height="20" viewBox="0 0 14 20"><path d="M7 1a6 6 0 0 1 6 6c0 4-6 12-6 12S1 11 1 7a6 6 0 0 1 6-6z" fill="#d8623a"/><circle cx="7" cy="7" r="2.2" fill="#fff"/></svg><span>Carrowfield,<br>MD</span></div>
</article>
<article class="card abs" style="left:609px;top:1561px">
  <div class="card-photo" role="img" aria-label="Glass-topped wooden coffee table" style="background:linear-gradient(160deg,#a89c8e,#d8d2c3 45%,#8f8a84)"></div>
  <h3 class="card-title">Curabitur luctus dignissim</h3><p class="card-text">Aenean lectus ligula, viverra vitae dui id</p>
  <div class="card-place"><svg width="14" height="20" viewBox="0 0 14 20"><path d="M7 1a6 6 0 0 1 6 6c0 4-6 12-6 12S1 11 1 7a6 6 0 0 1 6-6z" fill="#d8623a"/><circle cx="7" cy="7" r="2.2" fill="#fff"/></svg><span>Carrowfield,<br>MD</span></div>
</article>

<nav class="pagination abs">
  <span class="active">1</span><span>2</span><span>3</span><span>4</span><span>5</span><span>6</span><span>7</span><span>8</span><span>»</span><span class="gap">…</span><span>»»</span>
</nav>

<div class="rule abs" style="top:1972px"></div>
<h2 class="section-title affiliations abs">Affiliations</h2>
<div class="badges abs" aria-label="Affiliated associations">
  <span></span><span class="round"></span><span class="round"></span>
  <span></span><span></span><span class="round"></span>
</div>
<div class="vrule abs"></div>
<div class="mailing abs">
  <h2 class="section-title">Join our Mailing List</h2>
  <p>Praesent gravida metus a condimentum convallis. Etiam at tellus quis diam.</p>
</div>
<div class="mail-field abs">Enter your mail ID<span class="mail-go"><svg width="8" height="12" viewBox="0 0 8 12"><path d="M2 2l4 4-4 4" fill="none" stroke="#555" stroke-width="1.5"/></svg></span></div>
<div class="rule abs" style="top:2169px"></div>

<footer class="site-footer abs">
  <nav class="footer-nav abs">
    <a href="#">Home</a><span class="sep">|</span><a href="#">Auctions</a><span class="sep">|</span><a href="#">Appraisals</a><span class="sep">|</span><a href="#">Real Estate</a><span class="sep">|</span><a href="#">FAQ</a><span class="sep">|</span><a href="#">About Us</a><span class="sep">|</span><a href="#">Contact Us</a>
  </nav>
  <p class="copyright abs">Copyright © 2013 &nbsp;Nerith. &nbsp;&nbsp;All rights reserved.</p>
  <div class="social footer-social abs"><span></span><span></span><span></span><span></span></div>
  <a class="to-top abs" href="#">Top<span><svg width="10" height="12" viewBox="0 0 10 12"><path d="M5 11V2M1 5l4-4 4 4" fill="none" stroke="#aaa" stroke-width="1.6"/></svg></span></a>
  <div class="footer-brand abs"><span class="brand-mark"></span><span class="brand-name">Nerith</span></div>
  <nav class="footer-legal abs"><a href="#">Contact us</a><span>|</span><a href="#">Sitemap</a></nav>
</footer>

</body>
</html>
```